We are a recruitment company based in Norwich/Cambridge England.
I have included our company logo which we want to remain the same.

What we are looking for is a new creative Business card which will really stand out!!

Contact Information for Business Card

Harriet Dunmore
email: Harriet@plavex.co.uk
Address: Brackwell House
Fenmoor Enterprise Park
Partridge Way
Norwich
QB9 3KX
Tel:01632 960418

```html
<!DOCTYPE html>
<html lang="en">
<head>
<meta charset="utf-8">
<title>Plavex Business Card</title>
<link rel="stylesheet" href="https://fonts.googleapis.com/css2?family=Quicksand:wght@500;600;700&display=swap">
<style>
  :root {
    --page-bg: #e6e7e8;
    --card-bg: #ffffff;
    --brand-green: #9acd0e;
    --brand-grey: #8c8689;
    --text-dark: #3d3a3c;
    --divider: #d9d9d9;
  }
  * { box-sizing: border-box; margin: 0; padding: 0; }
  html, body {
    width: 1200px;
    height: 900px;
    overflow: hidden;
    background: var(--page-bg);
    font-family: "Quicksand", sans-serif;
  }
  .sheet {
    width: 1200px;
    height: 900px;
    display: flex;
    flex-direction: column;
    align-items: center;
    justify-content: center;
    gap: 36px;
  }
  .card {
    position: relative;
    width: 700px;
    height: 400px;
    background: var(--card-bg);
    border-radius: 18px;
    overflow: hidden;
    box-shadow: 0 6px 18px rgba(0, 0, 0, 0.12);
  }

  /* Brand name block */
  .brand {
    display: flex;
    align-items: center;
    gap: 14px;
  }
  .brand-dot {
    border-radius: 50%;
    background: var(--brand-green);
    flex: none;
  }
  .brand-name {
    font-weight: 700;
    color: var(--brand-grey);
    letter-spacing: -0.5px;
    line-height: 1;
  }

  /* Front card */
  .card-front .brand {
    position: absolute;
    left: 70px;
    top: 160px;
  }
  .card-front .brand-dot { width: 52px; height: 52px; }
  .card-front .brand-name { font-size: 46px; }

  .card-front .divider {
    position: absolute;
    left: 372px;
    top: 70px;
    width: 1px;
    height: 170px;
    background: var(--divider);
  }
  .contact {
    position: absolute;
    left: 400px;
    top: 62px;
    color: var(--text-dark);
    font-size: 16px;
    font-weight: 600;
    line-height: 1.45;
  }
  .contact-name {
    color: var(--brand-green);
    font-size: 22px;
    font-weight: 700;
    margin-bottom: 4px;
  }
  .contact-line {
    display: flex;
    align-items: center;
    gap: 8px;
  }
  .contact-line svg { flex: none; }
  .contact-address { margin-top: 10px; }

  .web-tab {
    position: absolute;
    right: 0;
    bottom: 0;
    width: 310px;
    height: 66px;
    background: var(--brand-green);
    border-top-left-radius: 22px;
    color: #ffffff;
    font-size: 20px;
    font-weight: 700;
    letter-spacing: 1.5px;
    display: flex;
    align-items: center;
    justify-content: center;
  }

  /* Back card */
  .card-back {
    display: flex;
    align-items: center;
    justify-content: center;
  }
  .card-back .brand-dot { width: 92px; height: 92px; }
  .card-back .brand-name { font-size: 84px; }
</style>
</head>
<body>
<main class="sheet">
  <section class="card card-front" aria-label="Business card front">
    <div class="brand">
      <span class="brand-dot"></span>
      <span class="brand-name">Plavex</span>
    </div>
    <div class="divider"></div>
    <div class="contact">
      <p class="contact-name">Harriet Dunmore</p>
      <p class="contact-line">
        <svg width="14" height="14" viewBox="0 0 24 24" aria-hidden="true"><path fill="#9acd0e" d="M6.6 10.8a15.1 15.1 0 0 0 6.6 6.6l2.2-2.2a1 1 0 0 1 1-.25 11.4 11.4 0 0 0 3.6.57 1 1 0 0 1 1 1V20a1 1 0 0 1-1 1A17 17 0 0 1 3 4a1 1 0 0 1 1-1h3.5a1 1 0 0 1 1 1c0 1.25.2 2.45.57 3.57a1 1 0 0 1-.25 1z"/></svg>
        01632 960418
      </p>
      <p class="contact-line">
        <svg width="14" height="11" viewBox="0 0 24 18" aria-hidden="true"><rect width="24" height="18" rx="2" fill="#9acd0e"/><path d="M2 2l10 8 10-8" fill="none" stroke="#ffffff" stroke-width="2"/></svg>
        Harriet@plavex.co.uk
      </p>
      <div class="contact-address">
        <p>Brackwell House</p>
        <p>Fenmoor Enterprise Park</p>
        <p>Partridge Way Norwich QB9 3KX</p>
      </div>
    </div>
    <div class="web-tab">www.plavex.co.uk</div>
  </section>

  <section class="card card-back" aria-label="Business card back">
    <div class="brand">
      <span class="brand-dot"></span>
      <span class="brand-name">Plavex</span>
    </div>
  </section>
</main>
</body>
</html>
```